Quality Monitoring Company Needs a New Site

We are an established company that has a fair number of clients but the site lacks current design standards that we'd like to keep up with. We'd like to mimic the same style of the site on plinkora.com, vetrumo.com, https://brindlecoffer.com/, etc. We'd also like to make sure the designer understands SEO Silos and how it effects the design elements. Attached is the structure that I'd like to follow for the pages. You don't need to design every single sub-page because they'll probably be fairly similar; however, I want to see at least 1 each. Please use the content on our current site for filler areas. Please try to do a good job of understanding what we do so you can use your best judgement on what is needed to be successful. Use our color scheme and the logo should be the side view but I included the AI just in case.
Updates

I am narrowing down on the field of designs that I have received. There are a lot of similarities between the designs I like and don't like. I'd also like to ensure that some of the inner pages get done in the next 5 days so I can see the creativity that is there as well. That is probably what is next -- getting a few inner pages completed so I can see what you can come up with (not based on our current website) because the current "front pages" are all so good and so close.

Industry/Entity Type

Telecommunications

Colors

Designer to choose colors to be used in the design.

Requirements
Must have
• SEO Silo Look and Feel
• Current Colors
Should not have
• No stockphotos whatsoever. NONE.

```html
<!DOCTYPE html>
<html lang="en">
<head>
<meta charset="utf-8">
<title>Sample Scorecards – Vocalyst</title>
<link href="https://fonts.googleapis.com/css2?family=Montserrat:wght@600;700&family=Poppins:wght@400;500;600&display=swap" rel="stylesheet">
<style>
:root{
  --navy:#0b2d5b;
  --accent:#12aee8;
  --bg:#f4f6fb;
  --ring:#e4effb;
  --ring-soft:#edf5fc;
  --row-hl:#dcebfb;
  --row-alt:#f3f3f3;
  --line:#d8dce4;
  --text:#1e2a3a;
  --muted:#555d6b;
  --white:#ffffff;
}
*{margin:0;padding:0;box-sizing:border-box}
html,body{width:965px;height:1200px;overflow:hidden}
body{background:var(--bg);font-family:'Poppins',sans-serif;color:var(--text);position:relative}
.abs{position:absolute}
.bg-rings{left:0;top:0}
.brand{left:112px;top:50px;display:flex;align-items:center;gap:6px;font-family:'Poppins',sans-serif;font-weight:600;font-size:16px;color:var(--navy)}
.brand-dot{width:12px;height:12px;border-radius:50%;background:var(--accent)}
.nav{top:63px;left:325px;font-size:10px;color:var(--text)}
.nav a{position:absolute;white-space:nowrap;color:inherit;text-decoration:none}
.call{left:727px;top:52px;display:flex;align-items:center;gap:7px}
.call-icon{width:30px;height:30px;border-radius:50%;background:var(--accent);display:flex;align-items:center;justify-content:center}
.call-num{font-family:'Montserrat',sans-serif;font-weight:700;font-size:11.5px;color:var(--navy)}
.title{left:114px;top:178px;font-family:'Montserrat',sans-serif;font-weight:700;font-size:24.5px;color:var(--navy)}
.title span{color:var(--accent);font-weight:600}
.title-rule{left:114px;top:219px;width:28px;height:2px;background:var(--accent)}
.subtitle{left:116px;top:235px;font-family:'Montserrat',sans-serif;font-weight:600;font-size:15px;color:var(--navy)}
.intro{left:116px;top:262px;width:365px;font-size:9px;line-height:15.4px;letter-spacing:.55px;color:var(--muted)}
.hero-art{left:511px;top:114px;width:326px;height:258px;border-radius:14px;background:linear-gradient(160deg,#c9e6fa 0%,#18aee6 55%,#0b3a6b 100%)}
.ghost-label{left:464px;top:393px;font-size:10.5px;color:var(--white);opacity:.85}
.accordion{left:142px;top:450px;width:681px;height:39px;background:var(--white);border-radius:20px;box-shadow:0 6px 18px rgba(11,45,91,.06);display:flex;align-items:center;padding:0 18px 0 11px}
.accordion-icon{width:25px;height:25px;border-radius:50%;border:1.3px solid var(--navy);display:flex;align-items:center;justify-content:center;margin-right:11px}
.accordion-title{font-family:'Montserrat',sans-serif;font-weight:700;font-size:11.5px;color:var(--navy);flex:1}
.score-card{left:142px;top:528px;width:681px;height:346px;background:var(--white);box-shadow:0 0 40px rgba(11,45,91,.05)}
.score-table{position:absolute;left:11px;top:12px;width:659px;border-collapse:collapse;table-layout:fixed;font-size:9.3px}
.score-table th{background:var(--navy);color:var(--white);height:34px;text-align:left;font-family:'Poppins',sans-serif;font-weight:600;font-size:11.5px;padding-left:17px;border-right:1px solid #34507a}
.score-table th.mark{padding:0;text-align:center}
.score-table th:last-child,.score-table td:last-child{border-right:none}
.score-table td{height:31.2px;padding-left:17px;border-right:1px solid var(--line);white-space:nowrap;letter-spacing:.2px}
.score-table td:nth-child(2){padding-left:16px}
.score-table tr.alt td{background:var(--row-alt)}
.score-table tr.hl td{background:var(--row-hl)}
.footer{left:0;top:984px;width:965px;height:216px;background:var(--navy);color:var(--white)}
.footer h3{position:absolute;top:46px;font-family:'Montserrat',sans-serif;font-weight:700;font-size:14px;color:var(--accent)}
.footer-links a{position:absolute;font-size:9.5px;color:var(--white);text-decoration:none}
.footer-contact{position:absolute;font-size:10.5px;line-height:19px;letter-spacing:.2px;display:flex;gap:7px}
.footer-brand{position:absolute;left:752px;top:84px;display:flex;align-items:center;gap:7px;font-weight:600;font-size:18px;color:var(--white)}
.footer-brand i{width:16px;height:16px;border-radius:50%;background:var(--accent);display:block}
.footer-rule{position:absolute;left:112px;top:178px;width:738px;height:1px;background:#2a4a78}
.copyright{position:absolute;left:0;width:965px;top:189px;text-align:center;font-size:10px}
</style>
</head>
<body>

<svg class="abs bg-rings" width="965" height="1200" aria-hidden="true">
  <circle cx="806" cy="125" r="300" fill="var(--ring-soft)"/>
  <circle cx="806" cy="125" r="216" fill="var(--ring)"/>
  <circle cx="806" cy="125" r="145" fill="var(--ring-soft)"/>
</svg>

<header>
  <div class="abs brand"><span class="brand-dot"></span>Vocalyst</div>
  <nav class="abs nav">
    <a style="left:0">Home</a>
    <a style="left:47px">Services</a>
    <a style="left:107px">Industries</a>
    <a style="left:173px">Pricing</a>
    <a style="left:224px">Team</a>
    <a style="left:272px">Blog</a>
    <a style="left:312px">Contact Us</a>
  </nav>
  <div class="abs call">
    <span class="call-icon">
      <svg width="12" height="12" viewBox="0 0 24 24"><path fill="#fff" d="M6.6 10.8a15.1 15.1 0 0 0 6.6 6.6l2.2-2.2a1 1 0 0 1 1-.25 11.4 11.4 0 0 0 3.6.57 1 1 0 0 1 1 1V20a1 1 0 0 1-1 1A17 17 0 0 1 3 4a1 1 0 0 1 1-1h3.5a1 1 0 0 1 1 1c0 1.25.2 2.45.57 3.57a1 1 0 0 1-.25 1z"/></svg>
    </span>
    <span class="call-num">800-555-0147</span>
  </div>
</header>

<section class="hero">
  <h1 class="abs title">Sample <span>Scorecards</span></h1>
  <div class="abs title-rule"></div>
  <h2 class="abs subtitle">Can Voice Analytics Do This?</h2>
  <p class="abs intro">Vocalyst’s quality assurance services cut across key industry verticals. We have the capability to customize scorecards to suit your specific industry and provide an integrated solution for diverse and geographically split processes.</p>
  <div class="abs hero-art" role="img" aria-label="Illustration of a rocket launching from a laptop screen among leaves, a gear, documents and a paper plane"></div>
  <div class="abs ghost-label">Mortgage</div>
</section>

<section class="scorecards">
  <div class="abs accordion">
    <span class="accordion-icon">
      <svg width="15" height="15" viewBox="0 0 24 24" fill="none" stroke="var(--navy)" stroke-width="1.6"><circle cx="12" cy="12" r="9"/><path d="M12 12l4-5"/><circle cx="12" cy="12" r="1.5" fill="var(--accent)" stroke="none"/></svg>
    </span>
    <span class="accordion-title">Call Tracking – Automotive</span>
    <svg width="11" height="8" viewBox="0 0 12 8"><path d="M1 1.5l5 4.5 5-4.5" fill="none" stroke="var(--navy)" stroke-width="2.2"/></svg>
  </div>

  <div class="abs score-card">
    <table class="score-table">
      <colgroup><col style="width:117px"><col style="width:153px"><col style="width:254px"><col style="width:48px"><col style="width:44px"><col style="width:43px"></colgroup>
      <thead>
        <tr><th>Section</th><th>Short Name</th><th>Long Question</th><th class="mark">YES</th><th class="mark">NO</th><th class="mark">NA</th></tr>
      </thead>
      <tbody>
        <tr class="hl"><td>Questionnaire</td><td>Define the caller</td><td>Was the caller a customer or client?</td><td></td><td></td><td></td></tr>
        <tr><td>Questionnaire</td><td>New Product Inquiry</td><td>Did the caller inquire about a new product?</td><td></td><td></td><td></td></tr>
        <tr class="alt"><td>Questionnaire</td><td>Lease Product Inquiry</td><td>Did the caller inquire about leasing?</td><td></td><td></td><td></td></tr>
        <tr><td>Questionnaire</td><td>Parts and Service</td><td>Did the caller asked for parts and service?</td><td></td><td></td><td></td></tr>
        <tr class="alt"><td>Questionnaire</td><td>Appointment Scheduled</td><td>Was an appointment scheduled?</td><td></td><td></td><td></td></tr>
        <tr class="hl"><td>Questionnaire</td><td>Price Inquiry</td><td>Was there a price inquiry?</td><td></td><td></td><td></td></tr>
        <tr class="alt"><td>Questionnaire</td><td>Testing Scheduled</td><td>Was testing scheduled?</td><td></td><td></td><td></td></tr>
        <tr><td>Questionnaire</td><td>Luxury package selected</td><td>Was the luxury package scheduled?</td><td></td><td></td><td></td></tr>
        <tr class="alt"><td>Questionnaire</td><td>Information provided</td><td>Was caller information provided?</td><td></td><td></td><td></td></tr>
      </tbody>
    </table>
  </div>
</section>

<footer class="abs footer">
  <h3 style="left:112px">Quick Links</h3>
  <div class="footer-links">
    <a style="left:112px;top:80px">Home</a>
    <a style="left:112px;top:96px">Services</a>
    <a style="left:112px;top:112px">System Details</a>
    <a style="left:112px;top:129px">Pricing</a>
    <a style="left:236px;top:80px">Team</a>
    <a style="left:236px;top:96px">Blog</a>
    <a style="left:236px;top:112px">Contact Us</a>
    <a style="left:236px;top:129px">Login</a>
  </div>
  <h3 style="left:370px">Contact Us</h3>
  <div class="footer-contact" style="left:371px;top:73px">
    <svg width="10" height="14" viewBox="0 0 10 14" style="margin-top:4px"><path d="M5 0a5 5 0 0 0-5 5c0 3.7 5 9 5 9s5-5.3 5-9a5 5 0 0 0-5-5zm0 7a2 2 0 1 1 0-4 2 2 0 0 1 0 4z" fill="#fff"/></svg>
    <span>4210 Harbor Lane<br>Fairview, CA 90000</span>
  </div>
  <div class="footer-contact" style="left:531px;top:73px">
    <svg width="12" height="12" viewBox="0 0 24 24" style="margin-top:4px"><path fill="#fff" d="M6.6 10.8a15.1 15.1 0 0 0 6.6 6.6l2.2-2.2a1 1 0 0 1 1-.25 11.4 11.4 0 0 0 3.6.57 1 1 0 0 1 1 1V20a1 1 0 0 1-1 1A17 17 0 0 1 3 4a1 1 0 0 1 1-1h3.5a1 1 0 0 1 1 1c0 1.25.2 2.45.57 3.57a1 1 0 0 1-.25 1z"/></svg>
    <span>800-555-0147</span>
  </div>
  <div class="footer-contact" style="left:531px;top:101px">
    <svg width="12" height="10" viewBox="0 0 12 10" style="margin-top:5px"><rect width="12" height="10" rx="1" fill="#fff"/><path d="M0.5 1l5.5 4.5L11.5 1" fill="none" stroke="var(--navy)" stroke-width="1.2"/></svg>
    <span>Hello@Vocalyst.com</span>
  </div>
  <div class="footer-brand"><i></i>Vocalyst</div>
  <div class="footer-rule"></div>
  <p class="copyright">Copyright © 2019 VOCALYST. All Rights Reserved.</p>
</footer>

</body>
</html>
```